Website redesign www.marigoldlawpc.com law firm site

Need to redesign the website that I currently have to look more modern and professional. Would also like to be able to make updates and post without having a huge hassle. See current www.marigoldlawpc.com. I just think that it looks very immature and it's very templated there's no ability for me to make posts or Add links or anything like that

Target Market(s)

California people looking for a powerhouse attorney in

Industry/Entity Type

Legal

Number of Pages Required

3 page

Font styles to use
Serif
Sans Serif

Colors
ec1f27
000000
ffffff

Requirements
Must have
• Must be mobile friendly. Must look professional and have ability to post links to other websites. Must have ability to post blogs or articles. Would like to be able to read my FeeTrove account and also have the ability to upload forms for people to download
Nice to have
• Simple design easy to use and not cluttered with too much text

```html
<!DOCTYPE html>
<html lang="en">
<head>
<meta charset="utf-8">
<title>Marigold Law P.C</title>
<link href="https://fonts.googleapis.com/css2?family=Cinzel:wght@400;600;700&family=Jost:wght@400;500;600&display=swap" rel="stylesheet">
<style>
:root{
  --red:#ec1f27;
  --black:#000000;
  --white:#ffffff;
  --ink:#222222;
  --body:#555555;
  --muted:#888888;
  --line:#dddddd;
  --grey-btn:#d9d9d9;
  --footer:#1a1a1a;
  --light-band:#efefef;
  --social:#3b6fb6;
}
*{margin:0;padding:0;box-sizing:border-box}
html,body{width:1200px;height:2799px;overflow:hidden;background:var(--white)}
body{position:relative;font-family:"Jost",Arial,sans-serif;color:var(--ink)}
.abs{position:absolute}

/* header */
.site-header{top:0;left:0;width:1200px;height:121px}
.brand{left:100px;top:36px;color:var(--red);font-family:"Jost",Arial,sans-serif;font-size:40px;font-weight:500;line-height:48px;white-space:nowrap}
.contact-strip{right:95px;top:44px;display:flex;gap:42px;font-size:16px;color:var(--ink)}
.contact-item{display:flex;align-items:center;gap:12px}
.contact-item svg{width:32px;height:32px}

/* nav */
.main-nav{top:121px;left:0;width:1200px;height:43px;background:var(--black);display:flex;padding-left:100px}
.main-nav a{font-family:"Cinzel",Georgia,serif;font-size:16px;color:var(--white);text-decoration:none;height:43px;line-height:43px;padding:0 32px;border-right:1px solid #333;letter-spacing:.5px;white-space:nowrap}
.main-nav a.active{background:var(--red)}
.main-nav a:last-child{border-right:0}

/* hero */
.hero{top:164px;left:0;width:1200px;height:517px;background:linear-gradient(120deg,#3a2414 0%,#8a5a2c 35%,#c99a55 60%,#5a3a1c 100%)}
.hero-caption{left:0;bottom:0;width:1200px;height:96px;background:linear-gradient(to bottom,rgba(0,0,0,.15),rgba(0,0,0,.75));color:var(--white);text-align:center;font-family:"Cinzel",Georgia,serif;font-size:23px;line-height:30px;padding-top:20px;letter-spacing:.5px}
.hero-arrow{top:232px;width:40px;height:30px;background:rgba(0,0,0,.6);display:flex;align-items:center;justify-content:center}

/* headings */
.section-title{display:flex;align-items:center;gap:10px;font-size:30px;font-weight:500;text-transform:uppercase;letter-spacing:.5px;color:var(--ink);white-space:nowrap}
.section-title .accent{color:var(--red)}
.title-icon{width:28px;height:24px;border-radius:3px;background:#bbbbbb}
.title-rule{height:1px;background:var(--line)}
.body-text{font-size:13.6px;line-height:24px;color:var(--body)}
.btn-grey{display:inline-block;background:var(--grey-btn);color:var(--ink);font-size:14px;font-weight:500;padding:0 20px;height:36px;line-height:36px;text-transform:uppercase}
.btn-red{background:var(--red);color:var(--white);font-size:14px;font-weight:500;text-transform:uppercase;text-align:center;height:36px;line-height:36px}

/* welcome */
.portrait-card{left:875px;top:728px;width:164px;height:192px;background:var(--red);padding:5px}
.portrait-photo{width:154px;height:146px;background:linear-gradient(#6a5a50,#3a2e28)}
.portrait-name{color:var(--white);text-align:center;font-size:15px;font-weight:500;line-height:32px;white-space:nowrap}

/* practice */
.practice{top:1017px;left:0;width:1200px;height:700px;background:radial-gradient(ellipse at center,#2e2e2e 0%,#141414 80%)}
.practice .section-title{color:var(--white)}
.tile{width:277px}
.tile-photo{height:172px;border:4px solid var(--white)}
.tile-label{height:42px;display:flex;align-items:center;justify-content:center;gap:10px;color:var(--white);font-size:15px;text-transform:uppercase}
.tile-label.on{background:var(--red)}
.tile-icon{width:14px;height:14px;border-radius:50%;background:var(--red)}
.tile-label.on .tile-icon{background:var(--white)}

/* inquiry */
.field{width:408px;height:34px;border:1px solid var(--line);font-size:12px;color:var(--muted);padding:0 14px;line-height:32px;margin-bottom:12px;position:relative}

/* blog */
.blog{top:2077px;left:0;width:1200px;height:433px;background:linear-gradient(var(--light-band),#f6f6f6)}
.card{width:263px;height:284px;background:var(--white);box-shadow:0 1px 3px rgba(0,0,0,.08)}
.card-photo{height:150px;position:relative}
.card-date{position:absolute;left:112px;bottom:-12px;width:38px;height:44px;background:var(--red);color:var(--white);text-align:center;font-size:17px;line-height:20px;padding-top:3px}
.card-date small{display:block;font-size:12px;border-top:1px solid rgba(255,255,255,.6);line-height:18px}
.card-meta{display:flex;justify-content:space-between;font-size:10px;color:var(--muted);padding:8px 14px 0}
.card-title{font-size:14px;font-weight:500;padding:6px 14px 0;color:var(--ink)}
.card-text{font-size:12.5px;line-height:20px;color:var(--body);padding:8px 14px 0}

/* footer */
.site-footer{top:2510px;left:0;width:1200px;height:248px;background:var(--footer);color:#cfcfcf}
.foot-title{font-size:17px;font-weight:500;color:var(--white);margin-bottom:10px}
.foot-links{list-style:none;font-size:12.5px;line-height:24px}
.foot-links li::before{content:"›";margin-right:9px}
.foot-text{font-size:12px;line-height:20px}
.social{display:flex;gap:6px;margin-top:10px}
.social span{width:22px;height:22px;background:var(--social)}
.map{left:789px;top:43px;width:250px;height:134px;background:linear-gradient(135deg,#cfe6c8,#9fc6e6)}
.copyright{top:2758px;left:0;width:1200px;height:41px;background:var(--red);color:var(--white);text-align:center;font-size:13px;line-height:41px}
</style>
</head>
<body>

<header class="site-header abs">
  <div class="brand abs">Marigold Law P.C</div>
  <div class="contact-strip abs">
    <div class="contact-item">
      <svg viewBox="0 0 32 32"><circle cx="16" cy="16" r="16" fill="#ec1f27"/><path d="M11 9l3 0 1.5 4-2 1.5a9 9 0 0 0 4 4l1.5-2 4 1.5 0 3a2 2 0 0 1-2 2A13 13 0 0 1 9 11a2 2 0 0 1 2-2z" fill="#fff"/></svg>
      (555) 555-0142
    </div>
    <div class="contact-item">
      <svg viewBox="0 0 32 32"><circle cx="16" cy="16" r="16" fill="#ec1f27"/><rect x="8" y="11" width="16" height="11" fill="#fff"/><path d="M8 11l8 6 8-6" fill="none" stroke="#ec1f27" stroke-width="1.5"/></svg>
      renee@themarigoldlawgroup.com
    </div>
  </div>
</header>

<nav class="main-nav abs">
  <a class="active">Home</a>
  <a>Attorney Profile</a>
  <a>Practice Areas ▾</a>
  <a>Client Reviews</a>
  <a>Links</a>
  <a>Contact Us</a>
</nav>

<section class="hero abs" role="img" aria-label="Gavel with handcuffs and open law books on a wooden desk">
  <div class="hero-arrow abs" style="left:0"><svg width="12" height="14"><path d="M9 1L2 7l7 6" fill="none" stroke="#fff" stroke-width="2"/></svg></div>
  <div class="hero-arrow abs" style="right:0"><svg width="12" height="14"><path d="M3 1l7 6-7 6" fill="none" stroke="#fff" stroke-width="2"/></svg></div>
  <div class="hero-caption abs">A Boutique Law Firm Opportunity For Clients Who Want To Enjoy All The<br>Advantages Of Renee's Broad Legal Experience And Education.</div>
</section>

<section class="welcome">
  <h2 class="section-title abs" style="left:162px;top:718px"><span class="title-icon" role="img" aria-label="Gavel icon"></span>Welcome to <span class="accent">Marigoldlawpc</span></h2>
  <div class="title-rule abs" style="left:200px;top:760px;width:640px"></div>
  <div class="body-text abs" style="left:162px;top:774px;width:680px">
    <p>Find the big firm style legal counsel you can work with in your hometown region at Marigold Law P.C., in Alder Falls. Attorney Renee L. Marigold, Esq., offers a boutique law firm opportunity for clients who want to enjoy all the advantages of her broad legal experience and education.</p>
    <p style="margin-top:10px">She works closely with clients, and has the knowledge of many areas of law to apply to your situation. This is very helpful when it is necessary to incorporate those different areas of law practice into creating a winning argument for your unique case.</p>
  </div>
  <span class="btn-grey abs" style="left:162px;top:936px">Read More &nbsp;›</span>
  <div class="portrait-card abs">
    <div class="portrait-photo" role="img" aria-label="Portrait of attorney Renee L. Marigold"></div>
    <div class="portrait-name">Renee L. Marigold</div>
  </div>
</section>

<section class="practice abs">
  <h2 class="section-title abs" style="left:0;width:1200px;justify-content:center;top:52px"><span class="title-icon" role="img" aria-label="Gavel icon"></span>Practice <span class="accent">Areas</span></h2>
  <div class="tile abs" style="left:162px;top:127px"><div class="tile-photo" role="img" aria-label="Business documents being signed" style="background:linear-gradient(#e8e8ea,#8a8c94)"></div><div class="tile-label on"><span class="tile-icon"></span>Business Law</div></div>
  <div class="tile abs" style="left:463px;top:127px"><div class="tile-photo" role="img" aria-label="Model house with contract and pen" style="background:linear-gradient(#555,#d8d8d8)"></div><div class="tile-label"><span class="tile-icon"></span>Real Estate Law</div></div>
  <div class="tile abs" style="left:763px;top:127px"><div class="tile-photo" role="img" aria-label="Gavel on bankruptcy petition" style="background:linear-gradient(#b06a3a,#e8e0d6)"></div><div class="tile-label"><span class="tile-icon"></span>Bankruptcy</div></div>
  <div class="tile abs" style="left:162px;top:375px"><div class="tile-photo" role="img" aria-label="Hands holding paper family cutout" style="background:linear-gradient(#e9c7b0,#b8876a)"></div><div class="tile-label"><span class="tile-icon"></span>Family Law</div></div>
  <div class="tile abs" style="left:463px;top:375px"><div class="tile-photo" role="img" aria-label="Person in handcuffs at a courtroom table" style="background:linear-gradient(#3a2a20,#8a5a38)"></div><div class="tile-label"><span class="tile-icon"></span>Criminal Law</div></div>
  <div class="tile abs" style="left:763px;top:375px"><div class="tile-photo" role="img" aria-label="Gavel in front of law book shelves" style="background:linear-gradient(#7a5a30,#2a1a12)"></div><div class="tile-label"><span class="tile-icon"></span>Civil Litigation</div></div>
  <div class="btn-red abs" style="left:489px;top:621px;width:224px">View All Practice Areas &nbsp;›</div>
</section>

<section class="account">
  <h2 class="section-title abs" style="left:162px;top:1750px"><span class="title-icon" role="img" aria-label="Gavel icon"></span>FeeTrove <span class="accent">Account</span></h2>
  <div class="title-rule abs" style="left:200px;top:1792px;width:369px"></div>
  <p class="body-text abs" style="left:162px;top:1804px;width:410px;font-size:13px">Ut wisi enim ad minim veniam, quis nostrud exerci tation ullamcorper suscipit lobortis nisl ut aliquip ex ea commodo consequat. Duis autem vel eum iriure dolor in hendrerit in vulputate velit esse molestie conse quat, vel illum dolore eu feugiat nulla facilisis at vero eros et accum san et iusto odio dignissim qui blandit praesent luptatum zzril delenit augue duis dolore te feugait nulla facilisi. Lorem ipsum dolor sit amet, consectetuer adipiscing elit, sed diam nonummy nibh...</p>
  <span class="btn-grey abs" style="left:162px;top:1999px">Read More &nbsp;›</span>

  <h2 class="section-title abs" style="left:631px;top:1750px"><span class="title-icon" role="img" aria-label="Gavel icon"></span>Quick <span class="accent">Inquiry</span></h2>
  <div class="title-rule abs" style="left:669px;top:1792px;width:370px"></div>
  <form class="abs" style="left:631px;top:1808px">
    <div class="field">Your Name</div>
    <div class="field">Subject<span style="position:absolute;right:12px">⌄</span></div>
    <div class="field">Your Email</div>
    <div class="field">Your Mobile No</div>
    <span class="btn-grey" style="margin-top:4px">Submit &nbsp;›</span>
  </form>
</section>

<section class="blog abs">
  <h2 class="section-title abs" style="left:0;width:1200px;justify-content:center;top:40px"><span class="title-icon" role="img" aria-label="Gavel icon"></span>Latest <span class="accent">Blog</span></h2>
  <article class="card abs" style="left:162px;top:106px">
    <div class="card-photo" role="img" aria-label="Signing a contract beside a model house" style="background:linear-gradient(#5a5e68,#c8c8c8)"><div class="card-date">07<small>May</small></div></div>
    <div class="card-meta"><span>Lena Ortiz</span><span>▭ 111 &nbsp; ♥ 160</span></div>
    <div class="card-title">Lorem ipsum dolor sit amet...</div>
    <p class="card-text">consectetuer adipiscing elit, sed diam nonummy nibh euismod tincidunt ut laoreet dolor er adipiscing elit,..[+]</p>
  </article>
  <article class="card abs" style="left:468px;top:106px">
    <div class="card-photo" role="img" aria-label="Gavel resting on a law book" style="background:linear-gradient(#8a4a2a,#d8c8b8)"><div class="card-date">07<small>May</small></div></div>
    <div class="card-meta"><span>Lena Ortiz</span><span>▭ 111 &nbsp; ♥ 160</span></div>
    <div class="card-title">Lorem ipsum dolor sit amet...</div>
    <p class="card-text">consectetuer adipiscing elit, sed diam nonummy nibh euismod tincidunt ut laoreet dolor er adipiscing elit,..[+]</p>
  </article>
  <article class="card abs" style="left:776px;top:106px">
    <div class="card-photo" role="img" aria-label="Hands sheltering a paper family" style="background:linear-gradient(#f2f2f2,#d6b8a4)"><div class="card-date">07<small>May</small></div></div>
    <div class="card-meta"><span>Lena Ortiz</span><span>▭ 111 &nbsp; ♥ 160</span></div>
    <div class="card-title">Lorem ipsum dolor sit amet...</div>
    <p class="card-text">consectetuer adipiscing elit, sed diam nonummy nibh euismod tincidunt ut laoreet dolor er adipiscing elit,..[+]</p>
  </article>
</section>

<footer class="site-footer abs">
  <div class="abs" style="left:162px;top:40px">
    <div class="foot-title">Quick Link</div>
    <ul class="foot-links"><li>Home</li><li>About Us</li><li>Practice Areas</li><li>Attorneys</li><li>Blog</li><li>Links</li><li>Contact Us</li></ul>
  </div>
  <div class="abs" style="left:347px;top:40px;width:190px">
    <div class="foot-title">Join Our Newsletter</div>
    <p class="foot-text">Subscribe to our Newsletter to get the latest scoop right to your inbox</p>
    <div style="margin-top:10px;width:186px;height:30px;background:#3a3a3a;color:#ddd;font-size:12px;line-height:30px;padding-left:12px">Enter Your Email</div>
    <div class="btn-red" style="margin-top:12px;width:114px;height:34px;line-height:34px;font-size:13px">Subscribe &nbsp;›</div>
  </div>
  <div class="abs" style="left:582px;top:40px">
    <div class="foot-title">Contact Detail</div>
    <p class="foot-text">418 Orchard Lane Suite 300<br>Alder Falls 00000<br>(555) 555-0142<br>renee@themarigoldlawgroup.com</p>
    <div class="social"><span></span><span></span><span></span><span></span></div>
  </div>
  <div class="map abs" role="img" aria-label="Street map showing the office location"></div>
  <div class="abs foot-text" style="left:789px;top:184px;text-decoration:underline">View Map</div>
</footer>
<div class="copyright abs">Copyright © 2016 Marigold Law Pc . All Right Reserved.</div>

</body>
</html>
```